I need a business card designed using the logo provided either vertical or horizontal......Harbourline Property Group is an Australian based real estate company that caters for the upper end of the market so the design of the business card "must reflect" the companies image!!
Colour combinations are optional but "must be realistic" and must be able to be accurately useable CMYK colours.
Please consider that any colours used "must be able to be used" and be suitable in following designs for "pull out banner signs" and "real estate signs".
The colours and the font in the attached designs are for example and other combinations are encouraged.
Target Market(s)
The High End of the Australian real estate market
Industry/Entity Type
Business
Contact Information for Business Card
Logo - Business Name - Director + Licensed Real Estate Agent - Mobile Number (Cell Phone) - Business Number - Fax - Email Address - Web address
Requirements
Must have
- Designs and colours (CMYK) that can easily be interpreted by an Australian printer.
Nice to have
- Some alternative ideas on colour and font..........the ones provided are ok and have been provided as an example but I am looking for alternative ideas
Should not have
- Loud, overly bright colours. Designs that do not reflect the professional standards of the business.
- Designs that look good on a computer monitor but can not be re-created on a printing press.............this is most important when it comes to shading etc.

```html
<!DOCTYPE html>
<html lang="en">
<head>
<meta charset="utf-8">
<title>Harbourline Property Group — Business Card</title>
<link rel="stylesheet" href="https://fonts.googleapis.com/css2?family=Source+Sans+3:wght@400;600;700&display=swap">
<style>
  :root {
    --backdrop: #1d1d1d;
    --card-top: #ffffff;
    --card-bottom: #eee8d9;
    --card-back: #ede6d5;
    --accent-orange: #e87a24;
    --brand-gold: #b07f35;
    --text-dark: #2b2b2b;
    --text-body: #3a3a3a;
  }
  * { margin: 0; padding: 0; box-sizing: border-box; }
  html, body {
    width: 1200px; height: 900px; overflow: hidden;
    background: var(--backdrop);
    font-family: "Source Sans 3", "Myriad Pro", sans-serif;
  }
  .stage { position: relative; width: 1200px; height: 900px; }
  .card {
    position: absolute; top: 311px; width: 430px; height: 248px;
    border-radius: 12px; overflow: hidden;
  }
  .card--front {
    left: 154px;
    background: linear-gradient(180deg, var(--card-top) 0%, var(--card-bottom) 100%);
  }
  .card--back { left: 632px; background: var(--card-back); }

  .front-brand {
    position: absolute; left: 40px; top: 70px; width: 150px;
    display: flex; align-items: center; gap: 10px;
  }
  .brand-square { width: 14px; height: 14px; background: var(--brand-gold); flex: none; }
  .front-brand .brand-name {
    color: var(--brand-gold); font-weight: 600; font-size: 21px; line-height: 1.15;
  }

  .contact { position: absolute; left: 208px; top: 46px; color: var(--text-body); }
  .contact__name { color: var(--accent-orange); font-weight: 700; font-size: 19px; line-height: 1.2; }
  .contact__role { font-size: 13px; line-height: 1.3; }
  .contact__address { margin-top: 12px; font-size: 12.5px; line-height: 1.15; }
  .contact__lines { margin-top: 12px; list-style: none; font-size: 12.5px; }
  .contact__lines li { display: flex; align-items: center; height: 16.3px; }
  .contact__lines svg { width: 9px; height: 9px; margin-right: 9px; fill: var(--accent-orange); }

  .back-brand {
    position: absolute; left: 0; right: 0; top: 0; bottom: 0;
    display: flex; align-items: center; justify-content: center; gap: 14px;
  }
  .back-brand .brand-square { width: 22px; height: 22px; }
  .back-brand .brand-name {
    color: var(--text-dark); font-weight: 600; font-size: 26px;
    letter-spacing: 1.5px; text-transform: uppercase; line-height: 1.1;
  }
</style>
</head>
<body>
<main class="stage">
  <section class="card card--front">
    <div class="front-brand">
      <span class="brand-square"></span>
      <span class="brand-name">Harbourline Property Group</span>
    </div>
    <div class="contact">
      <p class="contact__name">Daniel Whitmore</p>
      <p class="contact__role">Managing Director</p>
      <p class="contact__address">18 Wharf Street, Pyrmont<br>Sydney NSW, 2009</p>
      <ul class="contact__lines">
        <li><svg viewBox="0 0 10 10"><rect x="2.5" y="0" width="5" height="10" rx="1"/></svg>0412-555-018</li>
        <li><svg viewBox="0 0 10 10"><path d="M0 4 Q5 0 10 4 L8 5 L7 4 L3 4 L2 5 Z M2 6 H8 V10 H2 Z"/></svg>02-5550-1840</li>
        <li><svg viewBox="0 0 10 10"><path d="M1 3 H9 V10 H1 Z M3 0 H7 V3 H3 Z"/></svg>02-5550-1841</li>
        <li><svg viewBox="0 0 10 10"><path d="M0 2 H10 V9 H0 Z"/></svg>info@harbourline.au</li>
        <li><svg viewBox="0 0 10 10"><path d="M1 9 L4 6 L5 7 L2 10 Z M6 3 L9 0 L10 1 L7 4 Z M3 7 L7 3 L8 4 L4 8 Z"/></svg>www.harbourline.au</li>
      </ul>
    </div>
  </section>

  <section class="card card--back">
    <div class="back-brand">
      <span class="brand-square"></span>
      <span class="brand-name">Harbourline<br>Property Group</span>
    </div>
  </section>
</main>
</body>
</html>
```